Breakthrough Medical Device to Prevent Life-Threatening Respiratory Infections

Design a 4 page brochure using color scheme of LumaGuard logo. The brochure is for an advanced endotracheal tube that is able to prevent bacterial and fungal growth on its surfaces after being placed inside the patient's trachea. Endotracheal tubes are necessary to provide air to patients who cannot breather on their own. However, within hours of placing the endotracheal tube in the patient, bacteria and fungi in the patient's airway colonize the tube and form biofilms -- slime like aggregations that are resistant to antibiotics. These biofilms can dislodge from the tube and go into the patient's lungs causing potentially deadly infections.

Target Market(s)

Hospitals, Physicians

Industry/Entity Type

Medical Equipment

Font styles to use
Sans Serif

Colors
0455a3
33a6d7
ffffff

Requirements
Must have
• iimage of endotracheal tube, graphs from document sent, language in word file appropriately placed

```html
<!DOCTYPE html>
<html lang="en">
<head>
<meta charset="utf-8">
<title>LumaGuard Endotracheal Tube Brochure – Inner Spread</title>
<link href="https://fonts.googleapis.com/css2?family=Open+Sans:ital,wght@0,400;0,600;1,400&display=swap" rel="stylesheet">
<style>
  :root {
    --stage: #3a3a3a;
    --navy: #12356a;
    --navy-light: #4a71a0;
    --page: #ebecee;
    --page-shade: #d9dbde;
    --ink: #1b1b1b;
    --bar-dark: #151515;
    --bar-grey: #b5b5b5;
    --white: #ffffff;
    --accent: #33a6d7;
  }
  * { box-sizing: border-box; margin: 0; padding: 0; }
  html, body { width: 1200px; height: 833px; overflow: hidden; }
  body { background: var(--stage); font-family: "Open Sans", Arial, sans-serif; color: var(--ink); position: relative; }

  .spread { position: absolute; left: 60px; top: 40px; width: 1080px; height: 753px; display: flex; box-shadow: 0 12px 30px rgba(0,0,0,.45); }
  .page { position: relative; width: 540px; height: 753px; overflow: hidden;
    background: linear-gradient(135deg, var(--page) 0%, #f4f4f5 45%, var(--page-shade) 100%); }
  .page--left { box-shadow: inset -18px 0 24px -18px rgba(0,0,0,.25); }
  .page--right { box-shadow: inset 18px 0 24px -18px rgba(0,0,0,.25); }

  .band { position: absolute; left: 0; top: 0; width: 540px; }

  .benefits { position: absolute; list-style: none; color: var(--white); font-size: 13px; line-height: 1.25; }
  .benefits li { position: relative; padding-left: 20px; margin-bottom: 5px; }
  .benefits li svg { position: absolute; left: 0; top: 2px; }
  .page--left .benefits { left: 34px; top: 34px; width: 470px; }
  .page--right .benefits { left: 34px; top: 150px; width: 480px; }

  .placeholder { position: absolute; background: linear-gradient(135deg, #f7f7f8, #dcdde0); border-radius: 2px; }
  .molecule { left: 70px; top: 290px; width: 380px; height: 150px; }

  .chart { position: absolute; }
  .chart text { font-family: "Open Sans", Arial, sans-serif; fill: var(--ink); }

  .caption { position: absolute; font-size: 6.5px; line-height: 1.35; font-style: italic; color: #333; }
  .caption b { font-style: normal; font-weight: 600; }

  .micrographs { position: absolute; left: 300px; top: 412px; width: 200px; display: grid; grid-template-columns: 1fr 1fr; gap: 6px; }
  .micrographs .placeholder { position: static; height: 44px; background: linear-gradient(135deg, #6c6c6c, #2e2e2e); }
</style>
</head>
<body>
<div class="spread">

  <!-- Left page -->
  <section class="page page--left">
    <svg class="band" height="300" viewBox="0 0 540 300" aria-hidden="true">
      <defs>
        <linearGradient id="bandLeft" x1="0" y1="0" x2="1" y2="0.3">
          <stop offset="0" stop-color="#12356a"/>
          <stop offset="0.75" stop-color="#2a4f83"/>
          <stop offset="1" stop-color="#4a71a0"/>
        </linearGradient>
      </defs>
      <path d="M0 0 H540 V270 C380 225 190 200 0 190 Z" fill="url(#bandLeft)"/>
    </svg>
    <ul class="benefits">
      <li><svg width="12" height="12" viewBox="0 0 12 12"><path d="M2 6.5 L5 9.5 L10.5 2.5" fill="none" stroke="#fff" stroke-width="1.4"/></svg>Designed to Prevent bacterial and fungal colonization of all surfaces including the cuff</li>
      <li><svg width="12" height="12" viewBox="0 0 12 12"><path d="M2 6.5 L5 9.5 L10.5 2.5" fill="none" stroke="#fff" stroke-width="1.4"/></svg>No need for subglottic suctioning</li>
      <li><svg width="12" height="12" viewBox="0 0 12 12"><path d="M2 6.5 L5 9.5 L10.5 2.5" fill="none" stroke="#fff" stroke-width="1.4"/></svg>Prevents biofilm growth and related endotoxins for clinically-relevant time periods</li>
      <li><svg width="12" height="12" viewBox="0 0 12 12"><path d="M2 6.5 L5 9.5 L10.5 2.5" fill="none" stroke="#fff" stroke-width="1.4"/></svg>No need for human intervention</li>
      <li><svg width="12" height="12" viewBox="0 0 12 12"><path d="M2 6.5 L5 9.5 L10.5 2.5" fill="none" stroke="#fff" stroke-width="1.4"/></svg>Passive device</li>
      <li><svg width="12" height="12" viewBox="0 0 12 12"><path d="M2 6.5 L5 9.5 L10.5 2.5" fill="none" stroke="#fff" stroke-width="1.4"/></svg>Replacement for conventional ETT products</li>
    </ul>

    <div class="placeholder molecule" role="img" aria-label="Chemical structure diagram of the antimicrobial coating compound"></div>

    <!-- Figure 3 charts -->
    <svg class="chart" style="left:30px;top:460px" width="490" height="200" viewBox="0 0 490 200" aria-label="Figure 3 bar charts of biofilm growth over days">
      <g font-size="6">
        <!-- (a) -->
        <g transform="translate(0,0)">
          <text x="2" y="6">(a)</text>
          <path d="M18 10 V80 H150" fill="none" stroke="#222" stroke-width=".8"/>
          <rect x="28" y="22" width="18" height="58" fill="#151515"/><rect x="60" y="24" width="18" height="56" fill="#151515"/>
          <rect x="92" y="22" width="18" height="58" fill="#151515"/><rect x="116" y="26" width="8" height="54" fill="#b5b5b5" stroke="#222" stroke-width=".5"/>
          <text x="30" y="88">Day 5</text><text x="62" y="88">Day 6</text><text x="96" y="88">Day 7</text><text x="124" y="88">Day 8</text>
        </g>
        <!-- (b) -->
        <g transform="translate(165,0)">
          <text x="2" y="6">(b)</text>
          <path d="M18 10 V80 H150" fill="none" stroke="#222" stroke-width=".8"/>
          <rect x="28" y="22" width="18" height="58" fill="#151515"/><rect x="60" y="22" width="18" height="58" fill="#151515"/>
          <rect x="92" y="22" width="18" height="58" fill="#151515"/><rect x="116" y="72" width="8" height="8" fill="#b5b5b5" stroke="#222" stroke-width=".5"/>
          <text x="30" y="88">Day 5</text><text x="62" y="88">Day 7</text><text x="96" y="88">Day 8</text><text x="124" y="88">Day 9</text>
        </g>
        <!-- (c) -->
        <g transform="translate(330,0)">
          <text x="2" y="6">(c)</text>
          <path d="M18 10 V80 H150" fill="none" stroke="#222" stroke-width=".8"/>
          <rect x="28" y="22" width="18" height="58" fill="#151515"/><rect x="60" y="24" width="18" height="56" fill="#151515"/>
          <rect x="92" y="24" width="18" height="56" fill="#151515"/><rect x="124" y="48" width="14" height="32" fill="#b5b5b5" stroke="#222" stroke-width=".5"/>
          <text x="30" y="88">Day 1</text><text x="62" y="88">Day 2</text><text x="96" y="88">Day 3</text><text x="124" y="88">Day 4</text>
        </g>
        <!-- (d) -->
        <g transform="translate(0,100)">
          <text x="2" y="6">(d)</text>
          <path d="M18 10 V80 H150" fill="none" stroke="#222" stroke-width=".8"/>
          <rect x="28" y="20" width="18" height="60" fill="#151515"/><rect x="60" y="20" width="18" height="60" fill="#151515"/>
          <rect x="92" y="22" width="18" height="58" fill="#151515"/><rect x="122" y="56" width="10" height="24" fill="#b5b5b5" stroke="#222" stroke-width=".5"/>
          <text x="30" y="88">Day 5</text><text x="62" y="88">Day 7</text><text x="96" y="88">Day 9</text><text x="122" y="88">Day 10</text>
        </g>
        <!-- (e) -->
        <g transform="translate(165,100)">
          <text x="2" y="6">(e)</text>
          <path d="M18 10 V80 H150" fill="none" stroke="#222" stroke-width=".8"/>
          <rect x="28" y="20" width="18" height="60" fill="#151515"/><rect x="60" y="20" width="18" height="60" fill="#151515"/>
          <rect x="92" y="22" width="18" height="58" fill="#151515"/><rect x="120" y="56" width="12" height="24" fill="#b5b5b5" stroke="#222" stroke-width=".5"/>
          <text x="30" y="88">Day 5</text><text x="62" y="88">Day 6</text><text x="96" y="88">Day 7</text><text x="124" y="88">Day 8</text>
        </g>
      </g>
    </svg>
    <p class="caption" style="left:34px;top:660px;width:400px"><b>Figure 3.</b> Biofilms formed on ETT segments after the indicated days of incubation with daily medium exchange. Black bars, uncoated tube segments; grey bars, coated segments. (a) MRSA; (b) K. pneumoniae; (c) P. aeruginosa; (d) C. albicans; (e) C. auris.</p>
  </section>

  <!-- Right page -->
  <section class="page page--right">
    <svg class="band" height="420" viewBox="0 0 540 420" aria-hidden="true">
      <defs>
        <linearGradient id="bandRight" x1="0" y1="0.3" x2="1" y2="0">
          <stop offset="0" stop-color="#4a71a0"/>
          <stop offset="0.3" stop-color="#2a4f83"/>
          <stop offset="1" stop-color="#12356a"/>
        </linearGradient>
      </defs>
      <path d="M0 0 H540 V400 C400 360 200 320 0 300 Z" fill="url(#bandRight)"/>
    </svg>
    <ul class="benefits">
      <li><svg width="12" height="12" viewBox="0 0 12 12"><path d="M2 6.5 L5 9.5 L10.5 2.5" fill="none" stroke="#fff" stroke-width="1.4"/></svg>Highly lubricious coating reduces coefficient of friction by 30x</li>
      <li><svg width="12" height="12" viewBox="0 0 12 12"><path d="M2 6.5 L5 9.5 L10.5 2.5" fill="none" stroke="#fff" stroke-width="1.4"/></svg>Contains broad spectrum antimicrobial and anti-inflammatory compound that slowly elutes from coating upon exposure to body fluids</li>
      <li><svg width="12" height="12" viewBox="0 0 12 12"><path d="M2 6.5 L5 9.5 L10.5 2.5" fill="none" stroke="#fff" stroke-width="1.4"/></svg>Designed to reduce antibiotic use and length of stay in the ICU</li>
      <li><svg width="12" height="12" viewBox="0 0 12 12"><path d="M2 6.5 L5 9.5 L10.5 2.5" fill="none" stroke="#fff" stroke-width="1.4"/></svg>Clinical studies set for 2018</li>
      <li><svg width="12" height="12" viewBox="0 0 12 12"><path d="M2 6.5 L5 9.5 L10.5 2.5" fill="none" stroke="#fff" stroke-width="1.4"/></svg>For Investigational Use in the USA.</li>
    </ul>

    <!-- Figures 4 and 5 small charts -->
    <svg class="chart" style="left:24px;top:312px" width="270" height="190" viewBox="0 0 270 190" aria-label="Figures 4 and 5 bar charts of biofilm growth">
      <g stroke="#222" stroke-width=".6" fill="none">
        <path d="M8 4 V38 H84"/><path d="M96 4 V38 H172"/><path d="M184 4 V38 H260"/>
        <path d="M8 48 V82 H84"/><path d="M96 48 V82 H172"/>
        <path d="M8 128 V162 H84"/><path d="M96 128 V162 H172"/>
      </g>
      <g fill="#151515">
        <rect x="14" y="10" width="8" height="28"/><rect x="30" y="10" width="8" height="28"/><rect x="46" y="11" width="8" height="27"/><rect x="62" y="11" width="8" height="27"/>
        <rect x="102" y="10" width="8" height="28"/><rect x="118" y="10" width="8" height="28"/><rect x="134" y="11" width="8" height="27"/><rect x="150" y="12" width="8" height="26"/>
        <rect x="190" y="10" width="8" height="28"/><rect x="206" y="10" width="8" height="28"/><rect x="222" y="11" width="8" height="27"/><rect x="238" y="11" width="8" height="27"/>
        <rect x="14" y="54" width="8" height="28"/><rect x="30" y="54" width="8" height="28"/><rect x="46" y="55" width="8" height="27"/><rect x="62" y="55" width="8" height="27"/>
        <rect x="102" y="54" width="8" height="28"/><rect x="118" y="54" width="8" height="28"/><rect x="134" y="55" width="8" height="27"/><rect x="150" y="56" width="8" height="26"/>
        <rect x="14" y="134" width="8" height="28"/><rect x="30" y="134" width="8" height="28"/><rect x="46" y="135" width="8" height="27"/><rect x="62" y="135" width="8" height="27"/>
        <rect x="102" y="134" width="8" height="28"/><rect x="118" y="134" width="8" height="28"/><rect x="134" y="135" width="8" height="27"/><rect x="150" y="136" width="8" height="26"/>
      </g>
      <g fill="#b5b5b5"><rect x="72" y="32" width="5" height="6"/><rect x="160" y="30" width="5" height="8"/><rect x="248" y="31" width="5" height="7"/><rect x="72" y="76" width="5" height="6"/><rect x="160" y="75" width="5" height="7"/><rect x="72" y="155" width="5" height="7"/><rect x="160" y="154" width="5" height="8"/></g>
    </svg>
    <p class="caption" style="left:30px;top:400px;width:250px;font-size:5px"><b>Figure 4.</b> Bacterial biofilms on ETT segments over time. Black bars, uncoated; grey bars, coated segments.</p>
    <p class="caption" style="left:30px;top:482px;width:250px;font-size:5px"><b>Figure 5.</b> Mixed species biofilms on tube segments after incubation. Grey bars, coated segments.</p>

    <div class="micrographs">
      <div class="placeholder" role="img" aria-label="Electron micrograph of uncoated tube surface"></div>
      <div class="placeholder" role="img" aria-label="Electron micrograph of coated tube surface"></div>
      <div class="placeholder" role="img" aria-label="Electron micrograph of uncoated tube surface"></div>
      <div class="placeholder" role="img" aria-label="Electron micrograph of coated tube surface"></div>
      <div class="placeholder" role="img" aria-label="Electron micrograph of uncoated tube surface"></div>
      <div class="placeholder" role="img" aria-label="Electron micrograph of coated tube surface"></div>
    </div>
    <p class="caption" style="left:300px;top:564px;width:210px;font-size:5px"><b>Figure 7.</b> Electron micrographs of uncoated (left) and coated (right) tube surfaces after exposure.</p>

    <!-- Figure 6 chart -->
    <svg class="chart" style="left:40px;top:585px" width="470" height="135" viewBox="0 0 470 135" aria-label="Figure 6 bar chart of endotoxin quantities">
      <g font-size="6">
        <text transform="translate(12,95) rotate(-90)">Endotoxin units in growth medium (EU/mL)</text>
        <text transform="translate(452,112) rotate(-90)">Endotoxin units on ETT segments (EU/segment)</text>
        <path d="M50 6 V108 H400 V6" fill="none" stroke="#222" stroke-width=".8"/>
        <g text-anchor="end">
          <text x="46" y="110">0</text><text x="46" y="90">100</text><text x="46" y="70">200</text><text x="46" y="50">300</text><text x="46" y="30">400</text><text x="46" y="10">500</text>
        </g>
        <g>
          <text x="404" y="110">0</text><text x="404" y="90">1</text><text x="404" y="70">2</text><text x="404" y="50">3</text><text x="404" y="30">4</text><text x="404" y="10">5</text>
        </g>
        <rect x="70" y="107" width="26" height="1" fill="#151515"/>
        <rect x="150" y="88" width="26" height="20" fill="#151515"/><rect x="178" y="107" width="10" height="1" fill="#b5b5b5" stroke="#222" stroke-width=".4"/>
        <rect x="230" y="40" width="26" height="68" fill="#151515"/><rect x="258" y="105" width="10" height="3" fill="#b5b5b5" stroke="#222" stroke-width=".4"/>
        <rect x="310" y="24" width="26" height="84" fill="#151515"/><rect x="338" y="84" width="14" height="24" fill="#b5b5b5" stroke="#222" stroke-width=".4"/>
        <g text-anchor="middle">
          <text x="83" y="117">0 h</text><text x="168" y="117">4 h</text><text x="248" y="117">8 h</text>
          <text x="330" y="117">Endotoxin on ETT</text><text x="330" y="124">segments after 24 h</text>
          <text x="200" y="125">Endotoxin in growth medium at indicated times</text>
        </g>
      </g>
    </svg>
    <p class="caption" style="left:40px;top:722px;width:470px"><b>Figure 6.</b> Quantification of the amounts of endotoxin in the growth medium and on ETT segments after incubation with P. aeruginosa for the indicated time periods. Black bars, uncoated tube segments. Grey bars, coated tube segments.</p>
  </section>

</div>
</body>
</html>
```